Website for research group at university relating to human wildlife conflict

Australian university based research group. Researching the relationship between humans and wildlife, and seeking to explore ways for the two to coexist. The research group is called "Creature Harmony NexaForm lab" (NexaForm=coexistence, which should be spelled out somewhere)

I have a logo for the research group (from artflockly). it is attached. I like it when the logo can be used throughout the website (e.g for titles, and in backgrounds).

Just a simple and clean/modern feel. i like the following websites as examples, but also like to be a little different!
https://www.feralvantis.org/
http://www.qmbrn.org/

At least one large image on each page, like a banner (just put in one and i can replace them). Images of Australian wildlife preferred (especially canids), and images with humans and animals helps too.

I would like the following pages
Home page (including Vision statement; and link to twitter account).
THEN, the following pages- which can all be the same/similar design with minor differences according to content of that page.
People (inc photo and profile)
Publications (list of publications by topic)
Projects (details of projects- with title, photo, detail)
News items (by topic, with title, image, link)
Contact
Collaborators (list of groups and people we associated with group- name and photo)

Target Market(s)

government. researchers. university.

Industry/Entity Type

University

Coding

Coded - Design and coding required

Number of Pages Required

5+ page

Font styles to use
Sans Serif

Colors

Designer to choose colors to be used in the design.

Requirements
Must have
• I require all the coded files so that i have flexibility of where i can host it.
• must have my logo.
• must have a visually appealing, modern and easy to navigate landing page.
• must have a large photo (e.g banner) at the top of every page.
• must have twitter feed on home page.
Nice to have
• I require all the coded files so that i have the flexibility of where i can host it.

```html
<!DOCTYPE html>
<html lang="en">
<head>
<meta charset="utf-8">
<title>Creature Harmony NexaForm lab</title>
<link rel="stylesheet" href="https://fonts.googleapis.com/css2?family=Montserrat:wght@400;500;600;700&display=swap">
<style>
:root{
  --orange:#f06a35;
  --green:#4e6c28;
  --footer:#4d6a2a;
  --text:#555;
  --grey:#f4f4f4;
  --white:#fff;
}
*{box-sizing:border-box;margin:0;padding:0}
html,body{width:1200px;height:2375px;overflow:hidden}
body{position:relative;background:var(--white);font-family:Arial,Helvetica,sans-serif;color:var(--text)}
.abs{position:absolute}

.top-line{left:0;top:0;width:1200px;height:3px;background:var(--orange)}
.header{left:0;top:3px;width:1200px;height:108px;background:var(--white);box-shadow:0 2px 6px rgba(0,0,0,.12);z-index:2}
.nav{position:absolute;top:46px;left:0;font-family:'Montserrat',sans-serif;font-size:13px;font-weight:500;color:#333;letter-spacing:.2px}
.nav a{position:absolute;color:inherit;text-decoration:none;white-space:nowrap}
.nav a.active{color:var(--orange)}

.logo-badge{left:111px;top:2px;width:196px;height:196px;border-radius:50%;background:var(--white);z-index:3;display:flex;align-items:center;justify-content:center;text-align:center;padding:60px 18px 0}
.logo-badge span{font-family:'Montserrat',sans-serif;font-weight:700;font-size:17px;line-height:1.2;color:var(--orange)}

.hero{left:0;top:111px;width:1200px;height:612px;background:linear-gradient(100deg,#e58a2c 0%,#c86d22 35%,#8a4a1d 65%,#5e3417 100%)}
.hero-title{left:109px;top:332px;font-family:'Montserrat',sans-serif;font-weight:700;font-size:44px;line-height:54px;color:var(--white)}
.hero-sub{left:112px;top:458px;width:400px;font-family:'Montserrat',sans-serif;font-weight:600;font-size:14.5px;line-height:33px;color:var(--white)}

.heading{font-family:'Montserrat',sans-serif;font-weight:600;font-size:30px;color:var(--green);text-transform:uppercase;white-space:nowrap}
.heading em{font-style:normal;color:var(--orange)}
.body-text{font-size:12.5px;line-height:26.5px;text-align:justify}
.btn{display:flex;align-items:center;justify-content:center;background:var(--orange);color:var(--white);border-radius:24px;font-family:'Montserrat',sans-serif;font-weight:500;font-size:14px;text-transform:uppercase}

.news-title{font-family:'Montserrat',sans-serif;font-weight:600;font-size:16px;color:#333;text-transform:uppercase}
.news-date{width:125px;height:33px;border:1px solid var(--orange);color:var(--orange);font-family:'Montserrat',sans-serif;font-size:12px;display:flex;align-items:center;justify-content:center}
.news-text{width:364px;font-size:12.5px;line-height:25px}

.about{left:0;top:1173px;width:1200px;height:450px;background:var(--grey)}
.about-photo{left:138px;top:1213px;width:475px;height:354px;background:linear-gradient(135deg,#b9c98a,#7a8f4a 45%,#8a6a4c)}
.about-text{left:660px;top:1293px;width:396px;font-size:12px;line-height:25.6px}

.quote-mark{font-family:Georgia,serif;font-size:40px;color:#bbb}
.quote-text{left:211px;top:1699px;width:540px;font-size:12px;line-height:23px}
.quote-name{left:211px;top:1815px;font-family:'Montserrat',sans-serif;font-weight:500;font-size:15px;color:var(--orange);text-transform:uppercase}
.quote-date{left:212px;top:1838px;font-size:12.5px;color:#444}
.portrait{left:808px;top:1669px;width:196px;height:196px;border-radius:50%;border:4px solid #ccc;background:radial-gradient(circle at 50% 45%,#c89a7a,#6a4a38)}

.tweet-band{left:0;top:1917px;width:1200px;height:154px;background:var(--orange)}
.tweet-ring{left:156px;top:1941px;width:102px;height:102px;border-radius:50%;border:4px solid var(--white)}
.tweet-text{left:296px;top:1953px;width:720px;font-family:'Montserrat',sans-serif;font-size:12.5px;line-height:26px;color:var(--white);text-align:justify}
.tweet-text b{font-weight:400;color:#5a2a10}

.footer{left:0;top:2071px;width:1200px;height:304px;background:var(--footer)}
.footer-logo{left:400px;top:2084px;width:400px;text-align:center;font-family:'Montserrat',sans-serif;font-weight:700;font-size:20px;line-height:24px;color:var(--white)}
.footer-logo i{display:block;width:46px;height:46px;border-radius:50%;border:4px solid var(--white);margin:0 auto 8px}
.footer-rule{left:112px;top:2213px;width:975px;height:1px;background:rgba(255,255,255,.35)}
.social{top:2235px;width:60px;height:60px;border-radius:50%;border:1px solid rgba(255,255,255,.8);display:flex;align-items:center;justify-content:center}
.social svg{fill:none;stroke:#fff;stroke-width:1.5;stroke-linecap:round;stroke-linejoin:round}
.copyright{left:0;top:2327px;width:1200px;text-align:center;font-size:13px;color:var(--white)}
</style>
</head>
<body>
<div class="abs top-line"></div>
<header class="abs header">
  <nav class="nav">
    <a class="active" style="left:388px">HOME</a>
    <a style="left:469px">PEOPLE</a>
    <a style="left:560px">PUBLICATIONS</a>
    <a style="left:693px">PROJECTS</a>
    <a style="left:799px">NEWS</a>
    <a style="left:880px">COLLABORATORS</a>
    <a style="left:1029px">CONTACT</a>
  </nav>
</header>
<div class="abs logo-badge"><span>Creature Harmony NexaForm lab</span></div>

<section class="abs hero" role="img" aria-label="Banner photograph of a tiger walking through golden grassland"></section>
<h1 class="abs hero-title">CREATURE HARMONY<br>NEXAFORM LAB</h1>
<p class="abs hero-sub">Sed ut perspiciatis unde omnis iste natus error site voluptatem accusantium doloremque laudantium, totam rem aperiam</p>

<h2 class="abs heading" style="left:112px;top:768px">Our Mission <em>&amp; Vision</em></h2>
<div class="abs body-text" style="left:112px;top:831px;width:582px">
  <p>Sed ut perspiciatis unde omnis iste natus error sit voluptatem accusantium doloremque laudantium, totam rem aperiam, eaque ipsa quae ab illo inventore veritatis et quasi architecto beatae vitae dicta sunt explicabo. Nemo enim ipsam voluptatem quia voluptas sit aspernatur aut odit aut fugit, sed quia consequuntur magni dolores eos qui ratione voluptatem sequi nesciunt.</p>
  <p style="margin-top:27px">Neque porro quisquam est, qui dolorem ipsum quia dolor sit amet, consectetur, adipisci velit, sed quia non numquam eius modi tempora incidunt ut labore et dolore magnam aliquam quaerat voluptatem. Ut enim ad exercitationem ullam corporis suscipit laboriosam, nisi ut aliquid ex..</p>
</div>
<a class="abs btn" style="left:112px;top:1072px;width:140px;height:47px">Read More</a>

<h2 class="abs heading" style="left:723px;top:768px">Latest <em>News</em></h2>
<h3 class="abs news-title" style="left:723px;top:837px">Sed ut perspiciatis unde</h3>
<div class="abs news-date" style="left:723px;top:866px">JANUARY 21, 2019</div>
<p class="abs news-text" style="left:723px;top:911px">Sed ut perspiciatis unde omnis iste natus error sit voluptatem dolore mque laudantium, totam rem aperiam eaque ipsa...</p>
<h3 class="abs news-title" style="left:723px;top:989px">Sed ut perspiciatis unde</h3>
<div class="abs news-date" style="left:723px;top:1018px">JANUARY 21, 2019</div>
<p class="abs news-text" style="left:723px;top:1063px">Sed ut perspiciatis unde omnis iste natus error sit voluptatem dolore mque laudantium, totam rem aperiam eaque ipsa...</p>

<section class="abs about"></section>
<div class="abs about-photo" role="img" aria-label="Photo of a smiling group of friends taking a selfie outdoors"></div>
<h2 class="abs heading" style="left:660px;top:1233px">About <em>Us</em></h2>
<p class="abs body-text about-text">Sed ut perspiciatis unde omnis iste natus error sit voluptatem accusantium doloremque laudantium, totam rem aperiam, eaque ipsa quae ab illo inven tore veritatis et quasi architecto beatae vitae dicta sunt explicabo. Nemo enim ipsam voluptatem quia voluptas sit aspernatur aut odit aut fugit, sed magni dolores eos qui ratione voluptatem sequi nesciunt.Neque porro quisquam est, qui dolorem ipsum quia dolor sit amet, consectetur, adipisci magnam aliquam quaerat voluptatem.</p>
<a class="abs btn" style="left:659px;top:1496px;width:136px;height:49px">Read More</a>

<span class="abs quote-mark" style="left:190px;top:1670px">&ldquo;</span>
<p class="abs quote-text">Sed ut perspiciatis unde omnis iste natus error sit voluptatem accusantium doloremque laudantium, totam rem aperiam, eaque ipsa quae ab illo inventore veritatis et quasi architecto beatae vitae dicta sunt explicabo. Nemo enim ipsam voluptatem quia voluptas sit aspernatur aut odit aut fugit, sed quia consequuntur magni dolores eos qui ratione voluptatem sequi nesciunt.</p>
<span class="abs quote-mark" style="left:594px;top:1780px">&rdquo;</span>
<p class="abs quote-name">Mara Kellen</p>
<p class="abs quote-date">Posted On 07 July 2018</p>
<div class="abs portrait" role="img" aria-label="Round portrait photo of the quoted researcher"></div>

<section class="abs tweet-band"></section>
<div class="abs tweet-ring"></div>
<p class="abs tweet-text"><b>@harmonynexaformlab</b> ut perspiciatis unde omnis iste natus error sit voluptatem accusantium doloremque laudantium, totam rem aperiam, eaque ipsa quae <b>@harmonynexaformlab</b> ab illo inventore veritatis et quasi architecto beatae vitae dicta sunt explicabo. Nemo enim ipsam voluptatem quia voluptas sit aspernatur aut odit ...</p>

<footer class="abs footer"></footer>
<div class="abs footer-logo"><i></i>Creature Harmony<br>NexaForm lab</div>
<div class="abs footer-rule"></div>
<a class="abs social" style="left:386px" aria-label="Website">
  <svg width="18" height="18" viewBox="0 0 18 18"><circle cx="9" cy="9" r="7.5"/><path d="M1.5 9h15M9 1.5c2.5 2.5 2.5 12.5 0 15M9 1.5c-2.5 2.5-2.5 12.5 0 15"/></svg>
</a>
<a class="abs social" style="left:459px" aria-label="Messages">
  <svg width="18" height="16" viewBox="0 0 18 16"><path d="M2 1.5h14v9H7l-4 3.5v-3.5H2z"/></svg>
</a>
<a class="abs social" style="left:529px" aria-label="Share">
  <svg width="18" height="18" viewBox="0 0 18 18"><circle cx="4" cy="9" r="2.2"/><circle cx="14" cy="4" r="2.2"/><circle cx="14" cy="14" r="2.2"/><path d="M6 8l6-3M6 10l6 3"/></svg>
</a>
<a class="abs social" style="left:602px" aria-label="People">
  <svg width="18" height="18" viewBox="0 0 18 18"><circle cx="9" cy="6" r="3.5"/><path d="M2.5 17c0-4 3-6 6.5-6s6.5 2 6.5 6"/></svg>
</a>
<a class="abs social" style="left:671px" aria-label="Link">
  <svg width="18" height="18" viewBox="0 0 18 18"><path d="M7.5 10.5l3-3M6 8.5l-2 2a2.8 2.8 0 004 4l2-2M12 9.5l2-2a2.8 2.8 0 00-4-4l-2 2"/></svg>
</a>
<a class="abs social" style="left:744px" aria-label="Email">
  <svg width="18" height="14" viewBox="0 0 18 14"><rect x="1" y="1" width="16" height="12" rx="1"/><path d="M1 2l8 6 8-6"/></svg>
</a>
<p class="abs copyright">© Copyrights 2019 - Creature Harmony NexaForm lab.All Rights Reserved.</p>
</body>
</html>
```